Corvane Business Cards

Front of business card will have logo, name, address, & telephone number. Back of card will have a list of services provided - Roads, Substation Pads, Temporary Pads, Site Pads, Land Leveling, Powerline Row Cleaning, Land Clearing, Gates, Fencing, Construction Entrances, Excavation, Trenching, Underground Utilities, Directional Boring, Pile Driving. We are a construction company that uses heavy equipment like bulldozers, motor graders/blades, dump trucks, backhoes, hydro axes, & skid loaders. We build roads, pads, & install electric utility lines & waterlines underground. This logo is new. The word "Construction" can be smaller as uploaded 2 example edited logos. We will be using this card design for many employees.
Target Market(s)
Industrial Electric Powerline, Wind Turbine, Solar Panel, & Water Utility companies.
Contact Information for Business Card
Name/Position - Dwayne Halster - Owner
Address: 4875 FM 309
Merkel, TX 79412
Phone number - (325) 482-5096

```html
<!DOCTYPE html>
<html lang="en">
<head>
<meta charset="utf-8">
<title>Corvane Construction Business Cards</title>
<link rel="stylesheet" href="https://fonts.googleapis.com/css2?family=Arimo:wght@400;700&display=swap">
<style>
  :root {
    --maroon: #3b1119;
    --maroon-back: #391018;
    --paper: #ffffff;
    --backdrop: #d9d9d9;
    --rule: rgba(255,255,255,0.25);
  }
  * { margin: 0; padding: 0; box-sizing: border-box; }
  html, body { width: 1200px; height: 802px; overflow: hidden; }
  body {
    background: var(--backdrop);
    font-family: "Arimo", Arial, sans-serif;
    position: relative;
  }
  .card {
    position: absolute;
    top: 274px;
    width: 442px;
    height: 264px;
  }
  .card-front { left: 136px; background: var(--paper); color: var(--maroon); }
  .card-back { left: 624px; background: var(--maroon-back); color: #fff; text-align: center; }

  .brand { position: absolute; left: 26px; top: 58px; font-weight: 700; color: var(--maroon); }
  .brand-name { display: block; font-size: 34px; letter-spacing: 1px; line-height: 1; }
  .brand-tag { display: block; font-size: 19px; letter-spacing: 0.5px; margin-top: 34px; line-height: 1; }

  .phone-band {
    position: absolute; left: 177px; right: 0; top: 49px; height: 73px;
    background: var(--maroon); color: #fff;
    display: flex; align-items: center; justify-content: flex-end;
    padding-right: 22px; gap: 6px; font-size: 16px;
  }
  .phone-icon { width: 22px; height: 22px; }

  .person { position: absolute; left: 24px; top: 201px; }
  .person-name { font-size: 18px; font-weight: 700; text-transform: uppercase; }
  .person-role { font-size: 14px; margin-top: 2px; }
  .address { position: absolute; right: 24px; top: 208px; text-align: right; font-size: 14px; line-height: 16px; }

  .services, .about, .mission { position: absolute; left: 0; right: 0; font-size: 12.8px; line-height: 16.3px; }
  .services { top: 38px; }
  .about { top: 128px; }
  .mission { top: 203px; }
  .divider { position: absolute; left: 153px; width: 136px; height: 1px; background: var(--rule); }
  .divider-one { top: 114px; }
  .divider-two { top: 188px; }
</style>
</head>
<body>
  <section class="card card-front">
    <div class="brand">
      <span class="brand-name">CORVANE</span>
      <span class="brand-tag">CONSTRUCTION</span>
    </div>
    <div class="phone-band">
      <span class="phone-number">(325) 482-5096</span>
      <svg class="phone-icon" viewBox="0 0 24 24" aria-hidden="true">
        <circle cx="12" cy="12" r="10.5" fill="none" stroke="#fff" stroke-width="1.6"/>
        <path d="M9 6.5c.4 0 .7.2.8.5l.8 2c.1.3 0 .6-.2.8l-.9.8c.6 1.3 1.6 2.3 2.9 2.9l.8-.9c.2-.2.5-.3.8-.2l2 .8c.3.1.5.4.5.8v1.4c0 .6-.5 1-1 1C10.6 17.3 6.7 13.4 6.6 8.5c0-.6.4-1 1-1z" fill="none" stroke="#fff" stroke-width="1.4" stroke-linejoin="round"/>
      </svg>
    </div>
    <div class="person">
      <p class="person-name">Dwayne Halster</p>
      <p class="person-role">Owner</p>
    </div>
    <p class="address">4875 FM 309 Merkel<br>TX 79412</p>
  </section>

  <section class="card card-back">
    <p class="services">
      Roads | Substation Pads | Temporary Pads | Site Pads,<br>
      Land Leveling | Powerline Row Cleaning | Land Clearing<br>
      Gates | Fencing,Construction Entrances | Excavation<br>
      Trenching | Underground Utilities | Directional Boring | Pile Driving.
    </p>
    <div class="divider divider-one"></div>
    <p class="about">
      We are a construction company that uses heavy equipment<br>
      like bulldozers | motor graders/blades | dump trucks<br>
      backhoes | hydro axes &amp; skid loaders.
    </p>
    <div class="divider divider-two"></div>
    <p class="mission">
      We build roads, pads<br>
      install electric utility lines &amp; waterlines underground.
    </p>
  </section>
</body>
</html>
```